RiverPine - Rebranding, Namecard, Stationary and One Page Web

Refresh logo, make it modern and design matching name card, stationary and one page web

RiverPine Information Technology (Int'l) Company Limited
松河訊息科技(國際)有限公司

Company is System Integrator, and will be providing products and services to government and enterprise organizations. Our Chief Security Officer came from top U.S. vendor, and had been working on top enterprise and government projects globally, so we want the refreshed image of the new company to have a East Cost U.S. style, with hint of technology from Silicon Valley. The company will also be representing top brands from the U.S. on information security.

Branding refresh is needed because company is being acquired and is expanding

Target Market(s)

Cyber Security

Industry/Entity Type

Information Technology

Contact Information for Business Card

Need Chinese and English

Number of Pages Required

1 page

Font styles to use
Sans Serif

Colors
0292cd
00a990

Requirements
Must have
• Modern, clean, cyber look. Must keep same colors and general look and feel of original logo. Only modernization, do not change its personality

```html
<!DOCTYPE html>
<html lang="en">
<head>
<meta charset="utf-8">
<title>RiverPine Name Card</title>
<link rel="stylesheet" href="https://fonts.googleapis.com/css2?family=Open+Sans:wght@400;700&family=Tinos&family=Noto+Sans+TC:wght@400&display=swap">
<style>
  :root {
    --canvas: #e4e5e8;
    --paper: #ffffff;
    --brand-blue: #0292cd;
    --brand-teal: #00a990;
    --band-blue: #4a9cc7;
    --rule-green: #1fa58a;
    --ink: #3a3a3a;
    --ink-soft: #6a6a6a;
    --logo-dark: #1d5f9e;
  }
  * { box-sizing: border-box; margin: 0; padding: 0; }
  html, body { width: 1200px; height: 1200px; overflow: hidden; }
  body {
    background: var(--canvas);
    display: flex;
    flex-direction: column;
    align-items: center;
    justify-content: center;
    gap: 80px;
  }
  .card {
    position: relative;
    width: 840px;
    height: 480px;
    background: var(--paper);
    box-shadow: 0 6px 18px rgba(0,0,0,0.12);
    overflow: hidden;
  }
  /* front */
  .card-front .side-band {
    position: absolute; left: 0; top: 0; bottom: 0;
    width: 44px;
    background: linear-gradient(180deg, #5ba6cf, var(--band-blue));
  }
  .card-front .side-rule {
    position: absolute; left: 52px; top: 0; bottom: 0;
    width: 3px; background: var(--rule-green);
  }
  .contact {
    position: absolute; left: 100px; top: 150px;
    font-family: "Tinos", "Times New Roman", serif;
    color: var(--ink);
    font-size: 15px;
    line-height: 1.6;
  }
  .contact .name {
    font-family: "Open Sans", Arial, sans-serif;
    font-weight: 700;
    font-size: 32px;
    color: var(--brand-blue);
    letter-spacing: 0.5px;
    line-height: 1.2;
    margin-bottom: 6px;
  }
  .contact .name .title {
    font-family: "Tinos", serif;
    font-weight: 400;
    font-size: 15px;
    color: var(--ink);
    margin-left: 6px;
  }
  .contact .cn {
    font-family: "Noto Sans TC", sans-serif;
    color: var(--ink-soft);
    font-size: 15px;
  }
  .contact .phone {
    font-family: "Open Sans", Arial, sans-serif;
    font-weight: 700;
    letter-spacing: 1px;
    margin-top: 4px;
  }
  .contact .label { color: var(--brand-blue); }
  .front-mark {
    position: absolute; right: 70px; top: 172px;
    display: flex; align-items: center; gap: 12px;
    font-family: "Open Sans", Arial, sans-serif;
    font-weight: 700; font-size: 40px;
    color: var(--brand-blue);
  }
  .front-mark .dot {
    width: 22px; height: 22px; border-radius: 50%;
    background: var(--brand-teal);
  }
  /* back */
  .card-back {
    background: linear-gradient(150deg, var(--brand-blue) 0%, #1cb6d6 45%, var(--brand-teal) 100%);
    display: flex; align-items: center; justify-content: center;
  }
  .back-mark {
    display: flex; align-items: center; gap: 16px;
    font-family: "Open Sans", Arial, sans-serif;
    font-weight: 700; font-size: 64px;
    color: var(--logo-dark);
  }
  .back-mark .dot {
    width: 34px; height: 34px; border-radius: 50%;
    background: var(--logo-dark);
  }
</style>
</head>
<body>
  <section class="card card-front" aria-label="Name card front">
    <div class="side-band"></div>
    <div class="side-rule"></div>
    <div class="contact">
      <p class="name">DANIEL WONG<span class="title">CEO</span></p>
      <p>RiverPine Information Technology (Int'l) Company Limited</p>
      <p class="cn">松河訊息科技(國際)有限公司</p>
      <p class="phone">(852) 5120 4471</p>
      <p>www.hkriverpine.com.hk &nbsp;|&nbsp; danielwong@hkriverpine.com.hk</p>
      <p><span class="label">Office</span> – Room C, Unit 418, 4/F, Lok Wing</p>
      <p>Ind. Bldg, No 12 Sheung Yee Road, Kowloon Bay, Kowloon, HKSAR</p>
    </div>
    <div class="front-mark"><span class="dot"></span>RiverPine</div>
  </section>

  <section class="card card-back" aria-label="Name card back">
    <div class="back-mark"><span class="dot"></span>RiverPine</div>
  </section>
</body>
</html>
```